TK Homes - Stone Dorf Design

Looking for a double sides design, 1 side for my realestate and the other for home building. ( TK Homes on 1 side, Stone Dorf card on the other Side
Side 1 - Marek Tove ~ Vox Realty logo and Company ( the Property quarter )
Marek Tove
Marek@Marektove.example
IG - Marek_Bzq_Realtor
FB - marekt
Cell - 5558130467
3847 61 St Nw

Side 2
Marek Tove
5558130467
IG - Stonedorf_Bzq
Stonedorfdev@mailbox.example

Target Market(s)

Home buyers/ sellers

Industry/Entity Type

Home builders - Realestate

Contact Information for Business Card

Above

Requirements
Must have
• Black OR White background - my information -

```html
<!DOCTYPE html>
<html lang="en">
<head>
<meta charset="utf-8">
<title>Stone Dorf Design &amp; TK Homes – Business Cards</title>
<link rel="stylesheet" href="https://fonts.googleapis.com/css2?family=Tinos:wght@400;700&display=swap">
<style>
  :root {
    --page: #e9e6e1;
    --card: #000000;
    --blue: #0b72c0;
    --red: #e0514a;
    --white: #ffffff;
  }
  * { box-sizing: border-box; margin: 0; padding: 0; }
  html, body { width: 1200px; height: 780px; overflow: hidden; }
  body {
    background: var(--page);
    font-family: "Tinos", "Times New Roman", serif;
    position: relative;
  }
  .card {
    position: absolute;
    width: 560px;
    height: 320px;
    background: var(--card);
    border-radius: 26px;
    overflow: hidden;
    box-shadow: 0 10px 24px rgba(0,0,0,.28);
    color: var(--white);
  }
  .card--builder { left: 120px; top: 50px; }
  .card--realty  { left: 520px; top: 410px; }

  .card__bands, .card__divider { position: absolute; inset: 0; width: 100%; height: 100%; }

  .brand {
    position: absolute;
    left: 36px;
    top: 134px;
    width: 220px;
    display: flex;
    align-items: center;
    gap: 10px;
  }
  .brand__mark { width: 16px; height: 16px; background: var(--red); flex: none; }
  .brand__name {
    font-weight: 700;
    font-size: 36px;
    color: var(--blue);
    line-height: 1;
    white-space: nowrap;
  }

  .contact { position: absolute; left: 312px; top: 46px; }
  .contact--realty { top: 30px; }
  .contact__name { font-weight: 700; font-size: 32px; line-height: 1; white-space: nowrap; }
  .contact__first { color: var(--blue); }
  .contact__last { color: var(--red); }
  .contact__role { font-weight: 700; font-size: 16px; margin: 2px 0 14px 14px; }
  .contact__list { list-style: none; }
  .contact__item {
    display: flex; align-items: center; gap: 8px;
    font-size: 15px; line-height: 21px; white-space: nowrap;
  }
  .contact__icon { width: 14px; height: 14px; flex: none; }
  .contact__dot { width: 13px; height: 13px; border-radius: 50%; background: var(--blue); flex: none; }

  .address {
    position: absolute; left: 312px; top: 246px;
    font-size: 16px;
  }
</style>
</head>
<body>

  <!-- Home building side -->
  <section class="card card--builder">
    <svg class="card__divider" viewBox="0 0 560 320" aria-hidden="true">
      <line x1="258" y1="80" x2="300" y2="232" stroke="#fff" stroke-width="1.2"/>
    </svg>
    <div class="brand">
      <span class="brand__mark"></span>
      <span class="brand__name">Stone Dorf</span>
    </div>
    <div class="contact">
      <p class="contact__name"><span class="contact__first">Marek</span> <span class="contact__last">Tove</span></p>
      <p class="contact__role">Director</p>
      <ul class="contact__list">
        <li class="contact__item">
          <svg class="contact__icon" viewBox="0 0 24 24"><path fill="#0b72c0" d="M6.6 10.8a15 15 0 0 0 6.6 6.6l2.2-2.2c.3-.3.7-.4 1-.2 1.1.4 2.3.6 3.6.6.6 0 1 .4 1 1V20c0 .6-.4 1-1 1A17 17 0 0 1 3 4c0-.6.4-1 1-1h3.5c.6 0 1 .4 1 1 0 1.3.2 2.5.6 3.6.1.3 0 .7-.2 1z"/></svg>
          5558130467
        </li>
        <li class="contact__item"><span class="contact__dot"></span>Stonedorf_Bzq</li>
        <li class="contact__item">
          <svg class="contact__icon" viewBox="0 0 24 24"><rect x="2" y="5" width="20" height="14" fill="#0b72c0"/><path d="M2 5l10 8 10-8" fill="none" stroke="#000" stroke-width="1.6"/></svg>
          Stonedorfdev@mailbox.example
        </li>
      </ul>
    </div>
    <svg class="card__bands" viewBox="0 0 560 320" aria-hidden="true">
      <polygon points="330,278 560,278 560,300 360,300" fill="#0b72c0"/>
      <polygon points="0,300 350,300 328,320 0,320" fill="#e0514a"/>
    </svg>
  </section>

  <!-- Real estate side -->
  <section class="card card--realty">
    <svg class="card__divider" viewBox="0 0 560 320" aria-hidden="true">
      <line x1="258" y1="60" x2="300" y2="212" stroke="#fff" stroke-width="1.2"/>
    </svg>
    <div class="brand">
      <span class="brand__mark"></span>
      <span class="brand__name">Marek Tove</span>
    </div>
    <div class="contact contact--realty">
      <p class="contact__name"><span class="contact__first">Marek</span> <span class="contact__last">Tove</span></p>
      <p class="contact__role">Director</p>
      <ul class="contact__list">
        <li class="contact__item">
          <svg class="contact__icon" viewBox="0 0 24 24"><path fill="#0b72c0" d="M6.6 10.8a15 15 0 0 0 6.6 6.6l2.2-2.2c.3-.3.7-.4 1-.2 1.1.4 2.3.6 3.6.6.6 0 1 .4 1 1V20c0 .6-.4 1-1 1A17 17 0 0 1 3 4c0-.6.4-1 1-1h3.5c.6 0 1 .4 1 1 0 1.3.2 2.5.6 3.6.1.3 0 .7-.2 1z"/></svg>
          5558130467
        </li>
        <li class="contact__item"><span class="contact__dot"></span>marekt</li>
        <li class="contact__item"><span class="contact__dot"></span>Marek_Bzq_Realtor</li>
        <li class="contact__item">
          <svg class="contact__icon" viewBox="0 0 24 24"><rect x="2" y="5" width="20" height="14" fill="#0b72c0"/><path d="M2 5l10 8 10-8" fill="none" stroke="#000" stroke-width="1.6"/></svg>
          Marek@Marektove.example
        </li>
        <li class="contact__item">
          <svg class="contact__icon" viewBox="0 0 24 24"><circle cx="12" cy="12" r="10" fill="#0b72c0"/><path d="M2 12h20M12 2c3 3 3 17 0 20M12 2c-3 3-3 17 0 20" fill="none" stroke="#000" stroke-width="1.4"/></svg>
          www.marektove.example
        </li>
      </ul>
    </div>
    <p class="address">3847 61 St Nw</p>
    <svg class="card__bands" viewBox="0 0 560 320" aria-hidden="true">
      <polygon points="330,278 560,278 560,300 360,300" fill="#0b72c0"/>
      <polygon points="0,300 350,300 328,320 0,320" fill="#e0514a"/>
    </svg>
  </section>

</body>
</html>
```